Velmarotix - world unique technology for better life - please let them know who am i at first sight

We need a new business card for company which is a provider of unique crystal based technology suitable for all living being. For more information and final design you can use our brochure (our colours are black and blue from brochure).
We use Verdana font

Industry/Entity Type

Business

Contact Information for Business Card

regular dimension

Font styles to use
Other font styles liked:
• Verdana

Requirements
Must have
• Logo
• name
• function/position
• phone
• mobile
• e-mail
• adress
Nice to have
• inovative design (technology directed)

```html
<!DOCTYPE html>
<html lang="en">
<head>
<meta charset="utf-8">
<title>Velmarotix – Business Card</title>
<link href="https://fonts.googleapis.com/css2?family=Michroma&display=swap" rel="stylesheet">
<style>
  :root {
    --page-bg: #e4e7ea;
    --brand-blue: #2aaee6;
    --ink: #3a3d40;
    --ink-soft: #55595d;
    --swoosh-grey: #b4b7ba;
    --card-white: #ffffff;
    --card-fade: #e5e6e8;
  }
  * { margin: 0; padding: 0; box-sizing: border-box; }
  html, body {
    width: 1200px; height: 900px; overflow: hidden;
    background: var(--page-bg);
    font-family: "Michroma", Verdana, sans-serif;
  }
  .sheet {
    width: 1200px; height: 900px;
    display: flex; flex-direction: column; align-items: center; justify-content: center;
    gap: 40px;
  }
  .card {
    position: relative;
    width: 700px; height: 400px;
    border-radius: 34px;
    overflow: hidden;
    box-shadow: 0 10px 26px rgba(0,0,0,0.18);
  }
  .card--front { background: linear-gradient(160deg, var(--card-white) 35%, var(--card-fade) 100%); }
  .card--back { background: var(--brand-blue); }

  .card__waves { position: absolute; left: 0; bottom: 0; width: 700px; height: 400px; }

  .brand { position: absolute; display: flex; align-items: center; gap: 14px; }
  .brand__dot { width: 44px; height: 44px; border-radius: 50%; background: var(--brand-blue); }
  .brand__name { font-size: 30px; letter-spacing: 1px; color: var(--brand-blue); }
  .card--front .brand { top: 50px; left: 230px; }
  .card--back .brand { top: 160px; left: 50%; transform: translateX(-50%); }
  .card--back .brand__dot { background: var(--card-white); }
  .card--back .brand__name { color: var(--card-white); }

  .contact { position: absolute; top: 150px; left: 0; width: 700px; display: flex; }
  .contact__person {
    width: 340px; padding-right: 16px; text-align: right;
    font-size: 12.5px; line-height: 22px; color: var(--ink-soft);
    font-variant: small-caps;
  }
  .contact__name { font-size: 17px; color: var(--ink); letter-spacing: 1px; }
  .contact__role { margin-bottom: 6px; }
  .contact__divider { width: 1px; height: 118px; background: var(--ink-soft); }
  .contact__lines { padding-left: 14px; font-size: 12.5px; line-height: 22px; color: var(--ink-soft); list-style: none; }
  .contact__lines li { display: flex; align-items: center; gap: 8px; }
  .contact__icon { width: 14px; height: 14px; flex: none; }
</style>
</head>
<body>
<main class="sheet">

  <section class="card card--front" aria-label="Business card front">
    <svg class="card__waves" viewBox="0 0 700 400" aria-hidden="true">
      <path d="M0,250 C220,222 470,298 700,352 L700,400 L0,400 Z" fill="var(--swoosh-grey)"/>
      <path d="M0,264 C220,244 470,318 700,370 L700,400 L0,400 Z" fill="var(--card-white)"/>
      <path d="M0,276 C220,262 470,334 700,384 L700,400 L0,400 Z" fill="var(--brand-blue)"/>
    </svg>

    <div class="brand">
      <span class="brand__dot"></span>
      <span class="brand__name">VELMAROTIX</span>
    </div>

    <div class="contact">
      <div class="contact__person">
        <p class="contact__name">Daren Holt</p>
        <p class="contact__role">Owner · C.E.O</p>
        <p>Suite # 418, Orin Bldg,</p>
        <p>NY 10247</p>
      </div>
      <div class="contact__divider"></div>
      <ul class="contact__lines">
        <li>
          <svg class="contact__icon" viewBox="0 0 14 14" aria-hidden="true"><circle cx="7" cy="7" r="7" fill="var(--ink)"/><path d="M4.5,3.5 L6,5.5 L5.2,6.3 C5.8,7.5 6.6,8.3 7.7,8.8 L8.5,8 L10.5,9.5 L9.6,10.6 C6.6,10.3 3.7,7.4 3.4,4.4 Z" fill="#fff"/></svg>
          555-218-4470
        </li>
        <li>
          <svg class="contact__icon" viewBox="0 0 14 14" aria-hidden="true"><circle cx="7" cy="7" r="7" fill="var(--ink)"/><rect x="5" y="3" width="4" height="8" rx="0.8" fill="#fff"/></svg>
          555-630-1924
        </li>
        <li>
          <svg class="contact__icon" viewBox="0 0 14 14" aria-hidden="true"><circle cx="7" cy="7" r="7" fill="var(--ink)"/><rect x="3.5" y="6" width="7" height="4.5" fill="#fff"/><rect x="5" y="3.5" width="4" height="2.5" fill="#fff"/></svg>
          555-907-3358
        </li>
        <li>
          <svg class="contact__icon" viewBox="0 0 14 14" aria-hidden="true"><circle cx="7" cy="7" r="7" fill="var(--ink)"/><rect x="3.5" y="4.5" width="7" height="5" fill="#fff"/><path d="M3.5,4.5 L7,7.5 L10.5,4.5" fill="none" stroke="var(--ink)" stroke-width="0.8"/></svg>
          mail@velmarotix-tech.com
        </li>
        <li>
          <svg class="contact__icon" viewBox="0 0 14 14" aria-hidden="true"><circle cx="7" cy="7" r="7" fill="var(--ink)"/><circle cx="7" cy="7" r="3.6" fill="none" stroke="#fff" stroke-width="0.9"/><path d="M3.4,7 H10.6 M7,3.4 V10.6" stroke="#fff" stroke-width="0.8"/></svg>
          www.velmarotix-tech.com
        </li>
      </ul>
    </div>
  </section>

  <section class="card card--back" aria-label="Business card back">
    <div class="brand">
      <span class="brand__dot"></span>
      <span class="brand__name">VELMAROTIX</span>
    </div>
  </section>

</main>
</body>
</html>
```